Bespoke Builders Business Card Design

We need a business card for an established builder of high quality bespoke homes in Auckland and Northland. We build and renovate homes collaboratively facilitating effective communication between owners, builders, architects, suppliers and tradespeople. We have never built or renovated a home that leaks or has faults. We only use reliable materials. We have never been sued or had legal action taken against us. We are honest builders of bespoke homes not group mass produced homes. Our niche market is in character homes. We practice sustainability and have built a lot of coastal property. We have been in business for over thirty years . We would like to see natural colors of the environment sand,sea and maybe vegetation . The design should communicate quality, sustainability,fair pricing, open communication and the originality of bespoke building. And the fact that the builder is registered.

Industry/Entity Type

Business

Contact Information for Business Card

Rowan Tellick Builders
Ph. 021583917
18 Kestrel Rd Harwood Bay Auckland 0814
PO Box 927 Mangawhai 0583

```html
<!DOCTYPE html>
<html lang="en">
<head>
<meta charset="utf-8">
<title>Rowan Tellick Builders – Business Card</title>
<link rel="stylesheet" href="https://fonts.googleapis.com/css2?family=Old+Standard+TT:wght@700&family=Arimo:wght@400&display=swap">
<style>
  :root {
    --page-bg: #ecebe8;
    --card-white: #ffffff;
    --brand-navy: #1f2383;
    --card-black: #000000;
    --contact-text: #ffffff;
  }
  * { box-sizing: border-box; margin: 0; padding: 0; }
  html, body {
    width: 1189px;
    height: 1200px;
    overflow: hidden;
    background: var(--page-bg);
  }
  .sheet {
    position: relative;
    width: 1189px;
    height: 1200px;
  }
  .card {
    position: absolute;
    left: 140px;
    width: 917px;
    height: 523px;
    display: flex;
    flex-direction: column;
  }
  .card--top { top: 46px; }
  .card--bottom { top: 623px; }
  .card__brand {
    height: 271px;
    background: var(--card-white);
    display: flex;
    align-items: center;
    justify-content: center;
    padding-top: 24px;
  }
  .brand-name {
    font-family: "Old Standard TT", "Century Schoolbook", Georgia, serif;
    font-weight: 700;
    font-size: 68px;
    letter-spacing: 0.5px;
    color: var(--brand-navy);
    white-space: nowrap;
  }
  .card__stripe {
    height: 32px;
    background: var(--brand-navy);
  }
  .card__contact {
    flex: 1;
    background: var(--card-black);
    display: flex;
    flex-direction: column;
    align-items: center;
    padding-top: 44px;
    gap: 18px;
  }
  .contact-line {
    font-family: "Arimo", Arial, Helvetica, sans-serif;
    font-size: 26px;
    line-height: 30px;
    color: var(--contact-text);
    white-space: nowrap;
  }
</style>
</head>
<body>
  <main class="sheet">
    <section class="card card--top">
      <div class="card__brand"><h1 class="brand-name">Rowan Tellick Builders</h1></div>
      <div class="card__stripe"></div>
      <div class="card__contact">
        <p class="contact-line">021583917</p>
        <p class="contact-line">18 Kestrel Rd Harwood Bay Auckland 0814</p>
        <p class="contact-line">PO Box 927 Mangawhai 0583</p>
      </div>
    </section>
    <section class="card card--bottom">
      <div class="card__brand"><h2 class="brand-name">Rowan Tellick Builders</h2></div>
      <div class="card__stripe"></div>
      <div class="card__contact">
        <p class="contact-line">021583917</p>
        <p class="contact-line">18 Kestrel Rd Harwood Bay Auckland 0814</p>
        <p class="contact-line">PO Box 927 Mangawhai 0583</p>
      </div>
    </section>
  </main>
</body>
</html>
```